Online shopping portal - Business Card Design

Brivamart.com.au is a complete shopping experience. Search, compare & buy items from partnered stores & receive cashbash for your purchases and referrals.
Mission
Our mission is to provide a system for entrepreneurs to create an ongoing income, while providing consumers worldwide with a better way to shop.
A product brokerage and Internet marketing company that specialises in One-to-One Marketing, Quellon Oceania is a subsidiary of Dorvex Holdings Global, Inc.
With more than 3 million Preferred Customers and 180,000 Customer Managers worldwide, Dorvex Holdings has generated over $3 billion USD in accumulated retail sales. The Company employs more than 675 people globally with international operations in Australia, United States, Canada, Taiwan, Hong Kong, Mexico & Singapore
Through revolutionary technology and the one-to-one marketing and social shopping Quellon Oceania are leveraging the Internet with the power of people to create the economy of the future.
By providing online shoppers with the products and services they want and need — backed by the Company’s people power — Quellon Oceania is fast becoming the World Wide Web’s ultimate online shopping destination.
As a result, we are changing the way people shop and changing the economic paradigm where anyone can become financially independent by creating their own economy — Made with Goods. Driven by Folks®.
Description
Welcome to a new kind of comparison shopping site where you get PAID cashback to shop!
Simply create an account to start accumulating cash backs each time you make purchases across hundreds of trusted Partner Stores and thousands of your favorite brands through our convenient PixBasket® for one stop shopping.
All merchant stores are backed by GLIMVEN.NET's 100% satisfaction guarantee.

Updates
Project Deadline Extended
Reason: Hi all,  I am extending the deadline as i'm going to be away for my birthday (and may not have time to check before the current deadline anyway)  I figure that the more time i give you the better.

Industry/Entity Type
Online Shopping
Contact Information for Business Card
Business Name: Brivamart.com.au
website: www.brivamart.com.au
Facebook: www.facebook.com/brivamart.com.au.
Email: info@brivamart.com.au
Phone: Lorn on 0487 52 19 64
Requirements
Nice to have
- Create a Brivamart logo

```html
<!DOCTYPE html>
<html lang="en">
<head>
<meta charset="utf-8">
<title>Brivamart Business Card</title>
<link href="https://fonts.googleapis.com/css2?family=Jura:wght@500;600&display=swap" rel="stylesheet">
<style>
  :root {
    --navy: #15145c;
    --navy-deep: #0f0e48;
    --paper-light: #ffffff;
    --paper-shade: #e2e3e5;
    --ink-grey: #3a3a3a;
    --accent-gold: #b8901f;
    --backdrop: #2b2b2d;
    --white: #ffffff;
  }
  * { box-sizing: border-box; margin: 0; padding: 0; }
  html, body { width: 1200px; height: 870px; overflow: hidden; }
  body {
    background: var(--backdrop);
    font-family: "Jura", sans-serif;
    position: relative;
  }
  .card {
    position: absolute;
    left: 250px;
    width: 700px;
    height: 400px;
    overflow: hidden;
    background: linear-gradient(160deg, var(--paper-light) 0%, var(--paper-shade) 100%);
    box-shadow: 0 8px 24px rgba(0,0,0,0.45);
  }
  .card-back { top: 25px; }
  .card-front { top: 445px; }

  .brand {
    display: flex;
    align-items: center;
    gap: 12px;
    color: var(--navy);
    font-weight: 600;
    letter-spacing: 1px;
    white-space: nowrap;
  }
  .brand-square {
    width: 18px;
    height: 18px;
    background: var(--accent-gold);
    flex: none;
  }
  .card-back .brand {
    position: absolute;
    left: 0; right: 0; top: 0; bottom: 0;
    justify-content: center;
    font-size: 44px;
  }
  .card-front .brand {
    position: absolute;
    right: 44px;
    top: 96px;
    font-size: 34px;
  }

  .contact-list {
    position: absolute;
    left: 34px;
    top: 26px;
    list-style: none;
    color: var(--ink-grey);
    font-size: 15px;
    font-weight: 500;
  }
  .contact-list li {
    display: flex;
    align-items: center;
    gap: 10px;
    height: 30px;
    white-space: nowrap;
  }
  .contact-list svg { width: 15px; height: 15px; fill: var(--ink-grey); flex: none; }

  .info-band {
    position: absolute;
    left: 0; right: 0; bottom: 0;
    height: 178px;
    background: linear-gradient(180deg, var(--navy) 0%, var(--navy-deep) 100%);
    color: var(--white);
  }
  .address {
    position: absolute;
    left: 34px;
    top: 22px;
    font-size: 20px;
    font-weight: 500;
    line-height: 28px;
  }
  .person {
    position: absolute;
    right: 40px;
    bottom: 30px;
    text-align: right;
  }
  .person-name { font-size: 24px; font-weight: 600; letter-spacing: 1px; }
  .person-role { font-size: 18px; font-weight: 500; margin-top: 4px; }
</style>
</head>
<body>

<section class="card card-back">
  <div class="brand"><span class="brand-square"></span>BRIVAMART.COM.AU</div>
</section>

<section class="card card-front">
  <ul class="contact-list">
    <li>
      <svg viewBox="0 0 16 16"><path d="M3.5 1 6 3.8 4.8 5.6a9 9 0 0 0 5.6 5.6l1.8-1.2L15 12.5 13.2 15C6.8 14.5 1.5 9.2 1 2.8z"/></svg>
      0487 52 19 64
    </li>
    <li>
      <svg viewBox="0 0 16 16"><path d="M4 0h8a1 1 0 0 1 1 1v14a1 1 0 0 1-1 1H4a1 1 0 0 1-1-1V1a1 1 0 0 1 1-1zm1 2v10h6V2zm3 11a1 1 0 1 0 0 2 1 1 0 0 0 0-2z"/></svg>
      0412 73 58 20
    </li>
    <li>
      <svg viewBox="0 0 16 16"><path d="M4 0h7v5H4zM1 6h14v9H1zm3 2v2h2V8zm4 0v2h2V8zm-4 3v2h2v-2zm4 0v2h2v-2z"/></svg>
      0487 52 19 66
    </li>
    <li>
      <svg viewBox="0 0 16 16"><path d="M0 3h16v10H0zm1.5 1.3V5l6.5 4 6.5-4v-.7L8 8.2z"/></svg>
      info@brivamart.com.au
    </li>
    <li>
      <svg viewBox="0 0 16 16"><path d="M8 0a8 8 0 1 0 0 16A8 8 0 0 0 8 0zm0 1.4c.9.8 1.6 2.3 1.9 4.1H6.1C6.4 3.7 7.1 2.2 8 1.4zM1.5 7h3a13 13 0 0 0 0 2h-3a6.6 6.6 0 0 1 0-2zm4.5 0h4a11 11 0 0 1 0 2H6a11 11 0 0 1 0-2zm5.5 0h3a6.6 6.6 0 0 1 0 2h-3a13 13 0 0 0 0-2zM6.1 10.5h3.8c-.3 1.8-1 3.3-1.9 4.1-.9-.8-1.6-2.3-1.9-4.1z"/></svg>
      www.brivamart.com.au
    </li>
  </ul>

  <div class="brand"><span class="brand-square"></span>BRIVAMART.COM.AU</div>

  <div class="info-band">
    <p class="address">047, 9th floor, Plaza<br>Harrow Lane KTP</p>
    <div class="person">
      <p class="person-name">MARCUS WEYLAND</p>
      <p class="person-role">Managing Director</p>
    </div>
  </div>
</section>

</body>
</html>
```